KRV Business Card

Looking for a business card for my restaurant group I own. Four different concepts:

Copperfield Alehouse
Bristow Alehouse
Tanager's Stone Hearth Kitchen
Pellston Patty Company

Card doesn't need to include all the logos.

```html
<!DOCTYPE html>
<html lang="en">
<head>
<meta charset="utf-8">
<title>KRV Business Card</title>
<link href="https://fonts.googleapis.com/css2?family=Open+Sans:wght@400;600;700&display=swap" rel="stylesheet">
<style>
  :root {
    --page: #ebebeb;
    --card: #1b191a;
    --gold: #c9ad6e;
    --ink: #ffffff;
    --faint: #2a2623;
  }
  html, body {
    margin: 0;
    width: 1200px;
    height: 800px;
    overflow: hidden;
    background: var(--page);
    font-family: "Open Sans", Arial, sans-serif;
  }
  .card {
    position: absolute;
    left: 316px;
    width: 570px;
    height: 330px;
    background: var(--card);
    border-radius: 18px;
  }
  .card--front { top: 50px; }
  .card--back { top: 419px; }

  .brand-faint {
    position: absolute;
    left: 28px;
    top: 30px;
    margin: 0;
    font-size: 96px;
    font-weight: 700;
    line-height: 1;
    letter-spacing: 4px;
    color: var(--faint);
  }
  .brand {
    margin: 0;
    color: var(--gold);
    font-weight: 600;
    text-transform: uppercase;
    letter-spacing: 3px;
    line-height: 1.15;
  }
  .card--front .brand {
    position: absolute;
    right: 30px;
    top: 62px;
    text-align: right;
    font-size: 19px;
  }
  .card--back .brand {
    position: absolute;
    left: 0;
    right: 0;
    top: 112px;
    text-align: center;
    font-size: 34px;
    letter-spacing: 5px;
  }

  .person {
    position: absolute;
    left: 30px;
    top: 174px;
  }
  .person__name {
    margin: 0;
    color: var(--gold);
    font-size: 19px;
    font-weight: 600;
    line-height: 1.2;
  }
  .person__company {
    margin: 4px 0 0;
    color: var(--ink);
    font-size: 14px;
    line-height: 1.3;
  }
  .contact {
    list-style: none;
    margin: 12px 0 0;
    padding: 0;
  }
  .contact__item {
    display: flex;
    align-items: center;
    gap: 5px;
    height: 25px;
    color: var(--ink);
    font-size: 14px;
  }
  .contact__icon {
    width: 15px;
    height: 15px;
    flex: none;
  }
</style>
</head>
<body>
  <section class="card card--front">
    <p class="brand-faint" aria-hidden="true">KRV</p>
    <p class="brand">Kestrel Ridge<br>Ventures</p>

    <div class="person">
      <p class="person__name">Dana Holloway</p>
      <p class="person__company">Kestrel Ridge Ventures</p>
      <ul class="contact">
        <li class="contact__item">
          <svg class="contact__icon" viewBox="0 0 16 16" aria-hidden="true">
            <circle cx="8" cy="8" r="7.2" fill="none" stroke="var(--gold)" stroke-width="1"/>
            <path d="M5.3 4.6l1.3-.4.8 1.8-.8.7c.4.9 1 1.5 1.9 1.9l.7-.8 1.8.8-.4 1.3c-2.7.2-5.5-2.6-5.3-5.3z" fill="var(--gold)"/>
          </svg>
          555-014-2290
        </li>
        <li class="contact__item">
          <svg class="contact__icon" viewBox="0 0 16 16" aria-hidden="true">
            <circle cx="8" cy="8" r="7.2" fill="none" stroke="var(--gold)" stroke-width="1"/>
            <rect x="4.4" y="5.4" width="7.2" height="5.2" fill="var(--gold)"/>
            <path d="M4.4 5.6L8 8.4l3.6-2.8" fill="none" stroke="var(--card)" stroke-width="0.8"/>
          </svg>
          dana@krvrestaurants.com
        </li>
        <li class="contact__item">
          <svg class="contact__icon" viewBox="0 0 16 16" aria-hidden="true">
            <circle cx="8" cy="8" r="7.2" fill="none" stroke="var(--gold)" stroke-width="1"/>
            <circle cx="8" cy="8" r="3.8" fill="var(--gold)"/>
            <path d="M6 6.2c.8 0 1 .8 1.6 1 .5.3.2 1.1-.4 1.4M9.4 9.4c.4-.6 1-.5 1.2-.1" fill="none" stroke="var(--card)" stroke-width="0.8"/>
          </svg>
          www.krvrestaurants.com
        </li>
      </ul>
    </div>
  </section>

  <section class="card card--back">
    <p class="brand">Kestrel Ridge<br>Ventures</p>
  </section>
</body>
</html>
```